Laser Tattoo Removal Business Cards

We are looking for a professional business card design for a laser tattoo removal business. Ideally looking for a black business card design. The name of the business is Brightline Tattoo Removal. We place our cards at local tattoo shops so we ideally are looking for something trendy/edgy to draw both male and female clientele in.

Target Market(s)

Male/Female ages 18-60

Contact Information for Business Card

black background ideally.. hoping to stay within greys, whites and black

Font styles to use
Serif
Sans Serif

Colors
121212
a9a9a9
5c5c5c
f5f5f5
ffffff
7f7f7f
606060
848484
9d9d9d

Requirements
Must have
• Employee Info:
• Melissa Thornbury
• Chief Executive Offer
• m: 919.537.2846
• w: 919.362.4178
• f: 919.685.3907
• mthornbury@brightlinetattooremoval.example
• Address:
• 4615 Oakmere Pkwy, Suite 210
• Raleigh, NC 27654
• Website:
• www.brightlinetattooremoval.example
Nice to have
• Myabe business name on back or logo on back and employee info on the front

```html
<!DOCTYPE html>
<html lang="en">
<head>
<meta charset="utf-8">
<title>Brightline Tattoo Removal – Business Cards</title>
<link href="https://fonts.googleapis.com/css2?family=Raleway:wght@400;500;600;700&display=swap" rel="stylesheet">
<style>
  :root {
    --backdrop: #121212;
    --card: #ffffff;
    --ink: #121212;
    --ink-soft: #5c5c5c;
    --ink-muted: #606060;
    --rule: #a9a9a9;
    --photo-light: #f5f5f5;
    --photo-mid: #9d9d9d;
    --photo-dark: #1c1c1c;
  }
  * { box-sizing: border-box; margin: 0; padding: 0; }
  html, body {
    width: 1200px; height: 960px; overflow: hidden;
    background: var(--backdrop);
    font-family: "Raleway", Arial, sans-serif;
    color: var(--ink);
  }
  .card {
    position: absolute; left: 272px; width: 656px; height: 373px;
    background: var(--card); border-radius: 18px; overflow: hidden;
  }
  .card--front { top: 80px; }
  .card--back { top: 506px; }

  .brand {
    position: absolute; right: 40px; top: 48px; width: 190px;
    text-align: center; color: var(--ink); font-weight: 600;
    z-index: 2;
  }
  .brand__name { display: block; font-size: 31px; letter-spacing: 2px; text-transform: uppercase; line-height: 1; }
  .brand__line { display: block; margin-top: 12px; font-size: 13px; letter-spacing: 3px; text-transform: uppercase; }

  .person { position: absolute; left: 38px; top: 160px; }
  .person__name { font-size: 22px; font-weight: 700; letter-spacing: .3px; text-transform: uppercase; }
  .person__title { margin-top: 8px; font-size: 17px; font-weight: 500; color: var(--ink-muted); }

  .divider { position: absolute; left: 38px; right: 38px; top: 232px; border-top: 1.5px solid var(--rule); }

  .contact-list { position: absolute; left: 38px; top: 257px; list-style: none; }
  .contact-list li {
    display: flex; align-items: center; gap: 8px;
    height: 22px; font-size: 14px; font-weight: 500; color: var(--ink-soft);
  }
  .contact-list li.contact--email { font-size: 13px; }
  .contact-list svg { width: 12px; height: 12px; fill: var(--ink); flex: none; }

  .address { position: absolute; right: 38px; top: 257px; text-align: right; font-style: normal; }
  .address span { display: block; height: 22px; line-height: 22px; font-size: 14px; font-weight: 500; color: var(--ink-soft); }
  .website { position: absolute; right: 38px; top: 327px; font-size: 13px; font-weight: 500; color: var(--ink-soft); }
  .website strong { font-weight: 600; color: var(--ink); }

  .treatment-photo {
    position: absolute; left: 0; right: 0; top: 122px; bottom: 0;
    background:
      linear-gradient(180deg, rgba(255,255,255,1) 0%, rgba(255,255,255,0) 35%),
      linear-gradient(90deg, var(--photo-dark) 0%, #6e6e6e 30%, var(--photo-light) 55%, var(--photo-mid) 80%, var(--photo-dark) 100%);
  }
  .treatment-photo::after {
    content: ""; position: absolute; inset: 0;
    background: linear-gradient(180deg, rgba(0,0,0,0) 40%, rgba(18,18,18,.55) 100%);
  }
</style>
</head>
<body>

<section class="card card--front">
  <div class="brand">
    <span class="brand__name">Brightline</span>
    <span class="brand__line">Tattoo Removal</span>
  </div>

  <div class="person">
    <h1 class="person__name">Melissa Thornbury</h1>
    <p class="person__title">Chief Executive Offer</p>
  </div>

  <div class="divider"></div>

  <ul class="contact-list">
    <li>
      <svg viewBox="0 0 12 12" aria-hidden="true"><path d="M3.5 0.5h5a1 1 0 0 1 1 1v9a1 1 0 0 1-1 1h-5a1 1 0 0 1-1-1v-9a1 1 0 0 1 1-1zM4 2v7h4V2z"/></svg>
      919.537.2846
    </li>
    <li>
      <svg viewBox="0 0 12 12" aria-hidden="true"><path d="M3 1l2 2.5-1.2 1.2c.6 1.4 1.8 2.6 3.2 3.2L8.2 6.7 10.7 8.7 9.5 10.7C5.3 10.4 1.6 6.7 1.3 2.5z"/></svg>
      919.362.4178
    </li>
    <li>
      <svg viewBox="0 0 12 12" aria-hidden="true"><path d="M3 1h6v3H3zM1 5h10v4H9v2H3V9H1zM4 8v2h4V8z"/></svg>
      919.685.3907
    </li>
    <li class="contact--email">
      <svg viewBox="0 0 12 12" aria-hidden="true"><path d="M0.5 2.5h11v7h-11zM1.5 3.2l4.5 3.3 4.5-3.3z"/></svg>
      mthornbury@brightlinetattooremoval.example
    </li>
  </ul>

  <address class="address">
    <span>4615 Oakmere Pkwy, Suite 210</span>
    <span>Raleigh, NC 27654</span>
  </address>
  <p class="website">www.<strong>brightlinetattooremoval</strong>.example</p>
</section>

<section class="card card--back">
  <div class="brand">
    <span class="brand__name">Brightline</span>
    <span class="brand__line">Tattoo Removal</span>
  </div>
  <div class="treatment-photo" role="img" aria-label="Photo of a technician in gloves performing laser tattoo removal on a client's tattoo"></div>
</section>

</body>
</html>
```